Business Cards for new orthopaedic surgery practice

My husband and I are starting our own orthopaedic surgery practice. We are looking for a business card that is uniform, but one will have my name/title and the other will have his. You can just create one design with my name on it for now. But when I choose your design as the winning design I will ask that you add another copy with his name/title.

We are looking for classy, simple, elite all in one. We like dark blues/a little gold/yellow. Something that goes with our logo. We want our logo incorporated. Here is all the info you need:
Business name: RV Bone & Vitality Center
Location: 38517 North Willowmere Ave
Coral Springs, FL 33071
Phone: 954-218-4063
Fax: 954-582-7341
Email: info@myrvbonecare.example

Names: Lydia Vance, M.D.
Board Certified Hand and Upper Extremity Surgeon

Ebo Dansu, M.D.
Board Certified Hip & Knee Replacement/General Orthopaedic Surgeon

Can decide what you want to put on the back. Maybe a slogan:
Rooted in Care. Focused on You

I am just going to upload our logo. The only thing is if we select you as the winning design, the location, and phone numbers may change. We will need your help to update that once fully solidified.

Industry/Entity Type

Medical

Contact Information for Business Card

Colors
0054AA
0677BA
7BADD7
CADEEF
E8F1F8
0094D4
00A9DD
6FCCEA
C7EBF8
E9F6FB

Requirements
Must have
• class, appeal,
Should not have
• We want to air on the side of masculine if we are looking at masculine vs. feminine feel. But we still want it classy, sophisticated, and something we will love

```html
<!DOCTYPE html>
<html lang="en">
<head>
<meta charset="utf-8">
<title>RV Bone &amp; Vitality Center – Business Card</title>
<link href="https://fonts.googleapis.com/css2?family=Poppins:wght@400;500;600&display=swap" rel="stylesheet">
<style>
  :root {
    --navy: #1b2a50;
    --navy-soft: #2a3862;
    --gold: #c9a45c;
    --white: #ffffff;
    --backdrop: #e8ecee;
  }
  * { margin: 0; padding: 0; box-sizing: border-box; }
  html, body { width: 1200px; height: 960px; overflow: hidden; }
  body {
    background: var(--backdrop);
    font-family: "Poppins", sans-serif;
    position: relative;
  }
  .card {
    position: absolute;
    left: 248px;
    width: 703px;
    height: 402px;
    background: var(--navy);
    border-radius: 28px;
    overflow: hidden;
  }
  .card--front { top: 58px; }
  .card--back { top: 500px; }

  /* Front */
  .brand-mark {
    position: absolute;
    left: 0; right: 0;
    top: 130px;
    text-align: center;
    color: var(--white);
    font-weight: 500;
    font-size: 30px;
    line-height: 1.25;
    letter-spacing: 1px;
  }
  .slogan {
    position: absolute;
    left: 0; right: 0;
    top: 356px;
    text-align: center;
    color: var(--white);
    font-size: 15.5px;
    letter-spacing: 0.5px;
  }
  .slogan .dot {
    display: inline-block;
    width: 7px; height: 7px;
    border-radius: 50%;
    background: var(--gold);
    margin: 0 6px 2px 8px;
    vertical-align: middle;
  }

  /* Back */
  .brand-watermark {
    position: absolute;
    left: 30px;
    top: 60px;
    color: var(--navy-soft);
    font-weight: 600;
    font-size: 60px;
    line-height: 1.12;
  }
  .brand-badge {
    position: absolute;
    left: 549px;
    top: 58px;
    width: 140px;
    text-align: center;
    color: var(--white);
    font-weight: 500;
    font-size: 15px;
    line-height: 1.3;
  }
  .identity {
    position: absolute;
    right: 30px;
    top: 172px;
    text-align: right;
  }
  .identity__name {
    color: var(--gold);
    font-weight: 600;
    font-size: 22px;
    line-height: 1.2;
    letter-spacing: 0.5px;
  }
  .identity__title {
    color: var(--white);
    font-size: 15px;
    line-height: 1.4;
  }
  .accent-bar {
    position: absolute;
    left: 685px;
    top: 175px;
    width: 15px;
    height: 43px;
    background: var(--gold);
  }
  .address {
    position: absolute;
    right: 30px;
    top: 236px;
    text-align: right;
    color: var(--gold);
    font-size: 15.5px;
    line-height: 21px;
  }
  .contacts {
    position: absolute;
    right: 28px;
    top: 296px;
    list-style: none;
  }
  .contacts li {
    display: flex;
    justify-content: flex-end;
    align-items: center;
    gap: 10px;
    color: var(--white);
    font-size: 15.5px;
    height: 21px;
  }
  .contacts svg { width: 14px; height: 14px; flex: none; }
</style>
</head>
<body>

<section class="card card--front">
  <div class="brand-mark">RV Bone &amp;<br>Vitality Center</div>
  <p class="slogan"><span class="dot"></span>Rooted in Care <span class="dot"></span>Focused on You</p>
</section>

<section class="card card--back">
  <div class="brand-watermark">RV Bone &amp;<br>Vitality<br>Center</div>
  <div class="brand-badge">RV Bone &amp;<br>Vitality Center</div>

  <div class="identity">
    <div class="identity__name">Lydia Vance, M.D.</div>
    <div class="identity__title">Hand and Upper Extremity Surgery</div>
  </div>
  <div class="accent-bar"></div>

  <div class="address">38517 North Willowmere Ave<br>Coral Springs, FL 33071</div>

  <ul class="contacts">
    <li>954-218-4063
      <svg viewBox="0 0 24 24" fill="none" stroke="#c9a45c" stroke-width="2"><path d="M5 3h4l2 5-2.5 1.5a11 11 0 0 0 6 6L16 13l5 2v4a2 2 0 0 1-2 2A17 17 0 0 1 3 5a2 2 0 0 1 2-2z"/></svg>
    </li>
    <li>954-582-7341
      <svg viewBox="0 0 24 24" fill="none" stroke="#c9a45c" stroke-width="2"><rect x="3" y="9" width="18" height="11" rx="1"/><path d="M7 9V3h8l2 2v4"/><path d="M7 13h2M11 13h2M15 13h2M7 16h2M11 16h2M15 16h2"/></svg>
    </li>
    <li>www.myrvbonecare.example
      <svg viewBox="0 0 24 24" fill="none" stroke="#c9a45c" stroke-width="2"><circle cx="12" cy="12" r="9"/><path d="M3 12h18M12 3c3 3 3 15 0 18M12 3c-3 3-3 15 0 18"/></svg>
    </li>
    <li>info@myrvbonecare.example
      <svg viewBox="0 0 24 24" fill="none" stroke="#c9a45c" stroke-width="2"><rect x="3" y="6" width="18" height="13" rx="1"/><path d="M3 7l9 7 9-7"/></svg>
    </li>
  </ul>
</section>

</body>
</html>
```